Tour operator needs simple coded WordPress site (updated extra payment for coding and guaranteed)

[update 9/7/2015]
If you design a new logo and it gets accepted, even if we use another template with your logo you will get $50
[update 8/7/2015]
Update on questions about dual-language
For dual languages we are happy to set up a second site with the same designs in a second language.
For the design aspect just allow the user to switch between languages with an icon.
For the coding, a replica of the site on a second server will do (to save messing around with multiple language plugins) - we will populate it with Chinese text
[original post]
Simple coded WordPress site for tours
You can choose to design only or design and code ($340 design, $150 bonus for coding)
Open design brief - use your creativity
Will be in 2 languages (English and Chinese) but design needs only to be in one language
Winning design will be chosen only from home page, but the winner must make a second standard template page when chosen at no extra cost.
Must be responsive design
We only need homepage and standard template page design and coding, we will populate the pages
You can use design ideas from our pamphlet if you like - attached
Only a sample logo and colors on website and pamphlet - feel free to change as the current ones seem restrictive
Current website framework only to give an idea of the number of pages and basic menu structure (no need to use existing navigation style or any style at all for that matter, open brief)
http://brightwattlejourneys.com.au/
Target Market(s)
Chinese parents of kids 10-14 (the kids will take the tour)
Industry/Entity Type
Tour
Number of Pages Required
2 page
Look and feel
Each slider illustrates characteristics of the customer's brand and the style your logo design should communicate.

```html
<!DOCTYPE html>
<html lang="en">
<head>
<meta charset="utf-8">
<title>Bright Wattle Journeys</title>
<link rel="stylesheet" href="https://fonts.googleapis.com/css2?family=Open+Sans:wght@400;600;700&family=Oswald:wght@400;500&display=swap">
<style>
:root{
  --navy:#1d3a73;
  --navy-dark:#0f2347;
  --navy-deep:#0a1a38;
  --orange:#f39c1f;
  --yellow:#f5b800;
  --text:#555a63;
  --muted:#8a8f98;
  --light:#f1f2f4;
  --line:#d9dce1;
  --white:#ffffff;
}
*{box-sizing:border-box;margin:0;padding:0}
html,body{width:741px;height:1200px;overflow:hidden}
body{position:relative;background:var(--white);font-family:"Open Sans",Arial,sans-serif;color:var(--text);font-size:10px;line-height:1.45}
.abs{position:absolute}

/* header */
.site-header{left:0;top:0;width:741px;height:120px;background:linear-gradient(#fafafb,#eceef1)}
.brand{left:38px;top:12px;display:flex;align-items:center;gap:8px}
.brand-dot{width:46px;height:46px;border-radius:50%;background:var(--navy)}
.brand-name{font-weight:700;font-size:13px;color:var(--navy);line-height:1.1;width:90px}
.lang{right:20px;top:0;width:80px;height:20px;background:var(--navy);color:var(--white);font-size:9px;display:flex;align-items:center;justify-content:center;gap:5px}
.lang-flag{width:12px;height:8px;background:#7e8fb3}
.social{right:24px;top:30px;display:flex;gap:6px}
.social span{width:16px;height:16px;border-radius:3px;background:var(--navy)}
.nav{left:350px;top:68px;display:flex;height:28px;border:1px solid var(--line);background:var(--white);box-shadow:0 2px 4px rgba(0,0,0,.08)}
.nav a{display:flex;align-items:center;padding:0 22px;font-size:10px;font-weight:700;color:var(--navy);text-decoration:none;border-right:1px solid var(--line)}
.nav a:last-child{border-right:0}
.nav a.active{background:var(--navy);color:var(--white)}

/* slider */
.slider{left:20px;top:130px;width:700px;height:245px;background:linear-gradient(160deg,#8bb8de 0%,#c9a27a 55%,#6e4a3a 100%);box-shadow:0 6px 8px -4px rgba(0,0,0,.35)}
.caption{left:0;bottom:0;width:100%;height:36px;background:rgba(15,35,71,.55);display:flex;align-items:center;justify-content:space-between;padding:0 14px}
.caption p{font-family:"Oswald",sans-serif;font-size:17px;color:var(--white)}
.dots{display:flex;gap:5px}
.dots span{width:8px;height:8px;border-radius:50%;background:rgba(255,255,255,.55)}
.dots span.on{background:var(--white)}

/* about */
.section-title{font-size:14px;font-weight:700;color:var(--navy);letter-spacing:.3px}
.section-title em{font-style:normal;color:var(--orange)}
.rule{height:1px;background:var(--line);margin:8px 0 10px}
.about{left:45px;top:410px;width:435px}
.about .lead{font-weight:700;color:#3d424b;font-size:10px;margin-bottom:8px}
.btn{display:inline-block;background:var(--navy);color:var(--white);font-size:9px;font-weight:700;padding:5px 10px;text-decoration:none}
.about .btn{margin-top:10px}
.inquiry{left:505px;top:410px;width:195px}
.field{border:1px solid var(--line);height:18px;margin-bottom:6px;font-size:8px;color:var(--muted);padding:2px 6px;background:var(--white)}
.field.area{height:52px}

/* features */
.features{left:30px;top:610px;width:681px;display:flex;justify-content:space-between}
.feature{width:205px;text-align:center}
.icon{width:82px;height:82px;border-radius:50%;margin:0 auto 12px;display:flex;align-items:center;justify-content:center;border:4px solid #e3e6ea}
.icon.navy{background:var(--navy)}
.icon.yellow{background:var(--yellow)}
.icon.orange{background:var(--orange)}
.feature h3{font-size:11px;color:var(--navy);font-weight:700;margin-bottom:5px}
.feature p{font-size:9px;color:var(--muted);margin-bottom:6px}
.feature a{font-size:9px;font-weight:700;color:var(--navy)}

/* includes */
.includes{left:0;top:840px;width:741px;height:165px;background:var(--light);border-top:1px solid var(--line)}
.includes-body{left:45px;top:18px;width:440px}
.includes ul{list-style:none;display:grid;grid-template-columns:1fr 1fr;grid-auto-flow:column;grid-template-rows:repeat(5,auto);row-gap:4px}
.includes li{display:flex;align-items:center;gap:6px;font-size:9px}
.includes li svg{flex:none}
.brochure{left:505px;top:14px;width:195px;height:130px}
.brochure-photo{width:195px;height:104px;background:linear-gradient(150deg,#a9c6e2,#c48c6a 60%,#5c4a45)}
.brochure-bar{height:26px;background:var(--navy);color:var(--white);font-size:10px;font-weight:700;display:flex;align-items:center;justify-content:flex-end;padding-right:10px}

/* footer */
.footer{left:0;top:1005px;width:741px;height:170px;background:var(--navy-dark);color:#c9d0dd}
.footer h4{font-size:10px;font-weight:700;color:var(--white);margin-bottom:12px}
.col{top:20px}
.links{left:45px}
.links li{list-style:none;font-size:9px;margin-bottom:5px}
.subscribe{left:175px;width:150px}
.subscribe p{font-size:9px;margin-bottom:8px}
.subscribe .input{height:16px;background:var(--white);font-size:8px;color:var(--muted);padding:2px 5px;margin-bottom:6px}
.subscribe .go{display:inline-block;background:var(--yellow);color:var(--navy-dark);font-size:9px;font-weight:700;padding:3px 12px}
.contact{left:360px;width:190px}
.contact .row{display:flex;gap:8px;align-items:flex-start;font-size:9px;margin-bottom:10px}
.contact .row b{color:var(--white)}
.footer-brand{left:600px;top:60px;display:flex;align-items:center;gap:6px}
.footer-brand .brand-dot{width:32px;height:32px;background:var(--yellow)}
.footer-brand .brand-name{color:var(--white);font-size:10px;width:80px}
.copyright{left:0;top:1175px;width:741px;height:25px;background:var(--navy-deep);color:#9aa4b8;font-size:8px;display:flex;align-items:center;justify-content:center}
</style>
</head>
<body>

<header class="site-header abs">
  <div class="brand abs"><span class="brand-dot"></span><span class="brand-name">Bright Wattle Journeys</span></div>
  <div class="lang abs"><span class="lang-flag"></span>English ▾</div>
  <div class="social abs"><span></span><span></span><span></span></div>
  <nav class="nav abs">
    <a class="active" href="#">HOME</a><a href="#">ABOUT</a><a href="#">TOURS ▾</a><a href="#">CONTACT</a>
  </nav>
</header>

<section class="slider abs" role="img" aria-label="Group of smiling students on a city riverside with a bridge behind them">
  <div class="caption abs">
    <p>Educational, Safe, Culturally Bright Wattle Journeys Enlightening And Fun</p>
    <div class="dots"><span class="on"></span><span></span><span></span></div>
  </div>
</section>

<section class="about abs">
  <h2 class="section-title">ABOUT <em>BRIGHT WATTLE</em> JOURNEYS</h2>
  <div class="rule"></div>
  <p class="lead">At Bright Wattle Journeys We Are Passionate About Educational Travel And Opportunities For Students To Gain Academic And Cultural Understanding Of Australia.</p>
  <p>Hi day premium cultural and educational tours to Australian cities. Educational, safe, culturally enlightening and fun. Learn about educational institutions, history, sports, laws and customs, food and cuisine while improving your English.</p>
  <a class="btn" href="#">READ MORE</a>
</section>

<section class="inquiry abs">
  <h2 class="section-title"><em>QUICK</em> INQUIRY</h2>
  <div class="rule"></div>
  <div class="field">Name</div>
  <div class="field">Email</div>
  <div class="field area">Message</div>
  <a class="btn" href="#">SUBMIT</a>
</section>

<section class="features abs">
  <div class="feature">
    <div class="icon navy"><svg width="40" height="34" viewBox="0 0 40 34"><path d="M20 4 38 12 20 20 2 12Z" fill="#fff"/><path d="M10 16v8c4 4 16 4 20 0v-8l-10 4z" fill="#fff"/><path d="M35 13v10" stroke="#fff" stroke-width="2"/></svg></div>
    <h3>Educational And Cultural</h3>
    <p>Lorem ipsum dolor sit amet, consectetuer adipiscing elit, sed diam nonummy nibh euismod tincidunt ut laoreet dolore</p>
    <a href="#">READ MORE</a>
  </div>
  <div class="feature">
    <div class="icon yellow"><svg width="34" height="38" viewBox="0 0 34 38"><path d="M17 2 31 7v11c0 9-6 15-14 18C9 33 3 27 3 18V7Z" fill="none" stroke="#fff" stroke-width="3"/><path d="M10 19l5 5 9-10" fill="none" stroke="#fff" stroke-width="3"/></svg></div>
    <h3>Safe And Secure</h3>
    <p>Lorem ipsum dolor sit amet, consectetuer adipiscing elit, sed diam nonummy nibh euismod tincidunt ut laoreet dolore</p>
    <a href="#">READ MORE</a>
  </div>
  <div class="feature">
    <div class="icon orange"><svg width="38" height="38" viewBox="0 0 38 38"><path d="M35 5c-2-2-5-1-7 1l-6 6-16-4-3 3 13 7-6 6-5-1-2 2 6 4 4 6 2-2-1-5 6-6 7 13 3-3-4-16 6-6c2-2 3-5 1-7z" fill="#fff"/></svg></div>
    <h3>Travel Insurance</h3>
    <p>Lorem ipsum dolor sit amet, consectetuer adipiscing elit, sed diam nonummy nibh euismod tincidunt ut laoreet dolore</p>
    <a href="#">READ MORE</a>
  </div>
</section>

<section class="includes abs">
  <div class="includes-body abs">
    <h2 class="section-title">INCLUDES</h2>
    <div class="rule"></div>
    <ul>
      <li><svg width="10" height="10" viewBox="0 0 10 10"><rect width="10" height="10" fill="#f39c1f"/><path d="M2 5l2 2 4-4" stroke="#fff" stroke-width="1.5" fill="none"/></svg>Return tickets</li>
      <li><svg width="10" height="10" viewBox="0 0 10 10"><rect width="10" height="10" fill="#f39c1f"/><path d="M2 5l2 2 4-4" stroke="#fff" stroke-width="1.5" fill="none"/></svg>Visa fees</li>
      <li><svg width="10" height="10" viewBox="0 0 10 10"><rect width="10" height="10" fill="#f39c1f"/><path d="M2 5l2 2 4-4" stroke="#fff" stroke-width="1.5" fill="none"/></svg>Travel accident insurance</li>
      <li><svg width="10" height="10" viewBox="0 0 10 10"><rect width="10" height="10" fill="#f39c1f"/><path d="M2 5l2 2 4-4" stroke="#fff" stroke-width="1.5" fill="none"/></svg>Accommodation</li>
      <li><svg width="10" height="10" viewBox="0 0 10 10"><rect width="10" height="10" fill="#f39c1f"/><path d="M2 5l2 2 4-4" stroke="#fff" stroke-width="1.5" fill="none"/></svg>Meals (breakfast, lunch and dinner)</li>
      <li><svg width="10" height="10" viewBox="0 0 10 10"><rect width="10" height="10" fill="#f39c1f"/><path d="M2 5l2 2 4-4" stroke="#fff" stroke-width="1.5" fill="none"/></svg>Transportation</li>
      <li><svg width="10" height="10" viewBox="0 0 10 10"><rect width="10" height="10" fill="#f39c1f"/><path d="M2 5l2 2 4-4" stroke="#fff" stroke-width="1.5" fill="none"/></svg>Courses and Lectures</li>
      <li><svg width="10" height="10" viewBox="0 0 10 10"><rect width="10" height="10" fill="#f39c1f"/><path d="M2 5l2 2 4-4" stroke="#fff" stroke-width="1.5" fill="none"/></svg>Guides</li>
      <li><svg width="10" height="10" viewBox="0 0 10 10"><rect width="10" height="10" fill="#f39c1f"/><path d="M2 5l2 2 4-4" stroke="#fff" stroke-width="1.5" fill="none"/></svg>Entry tickets and travel expenses</li>
    </ul>
  </div>
  <div class="brochure abs">
    <div class="brochure-photo" role="img" aria-label="Students gathered together on a tour outing"></div>
    <div class="brochure-bar">Download Our Brochure ›</div>
  </div>
</section>

<footer class="footer abs">
  <div class="col links abs">
    <h4>QUICK LINKS</h4>
    <ul><li>› HOME</li><li>› ABOUT</li><li>› TOURS</li><li>› CONTACT US</li></ul>
  </div>
  <div class="col subscribe abs">
    <h4>SUBSCRIBE TO NEWSLETTER</h4>
    <p>Get Latest Updates By Entering Your Email Address</p>
    <div class="input">Email Address</div>
    <span class="go">Subscribe</span>
  </div>
  <div class="col contact abs">
    <h4>CONTACT DETAILS</h4>
    <div class="row"><svg width="10" height="13" viewBox="0 0 10 13"><path d="M5 0a5 5 0 0 0-5 5c0 4 5 8 5 8s5-4 5-8a5 5 0 0 0-5-5zm0 7a2 2 0 1 1 0-4 2 2 0 0 1 0 4z" fill="#f5b800"/></svg><span><b>BRIGHT WATTLE JOURNEYS</b><br>consectetuer adipiscing elit, sed diam nonummy</span></div>
    <div class="row"><svg width="11" height="11" viewBox="0 0 11 11"><path d="M2 0 4 3 3 4c1 2 2 3 4 4l1-1 3 2-1 2C5 11 0 6 0 1Z" fill="#f5b800"/></svg><span>02 5550 1842</span></div>
    <div class="row"><svg width="12" height="9" viewBox="0 0 12 9"><rect width="12" height="9" fill="#f5b800"/><path d="M0 0l6 5 6-5" stroke="#0f2347" fill="none"/></svg><span>info@brightwattlejourneys.com.au</span></div>
  </div>
  <div class="footer-brand abs"><span class="brand-dot"></span><span class="brand-name">Bright Wattle Journeys</span></div>
</footer>
<div class="copyright abs">© 2015 BRIGHT WATTLE JOURNEYS. ALL RIGHTS RESERVED.</div>

</body>
</html>
```